Mosquito and outdoor pest management

The uploaded logo must be integrated as the main theme of the card. I would like it to be modern and eye catching. Maybe some backround images or light silver metallic background.
Space enough at the base for contact info to be put in- phone numbers,emails,names,website.
Space on the back for short blog and lines for hand writing..calling card.
Commercial- golf courses, schools, outdoor function properties, pre event treatments.
Residential- retirement villages, townhome complexes and general houses
Management

```html
<!DOCTYPE html>
<html lang="en">
<head>
<meta charset="utf-8">
<title>Bayline Pest Care – Business Card</title>
<link href="https://fonts.googleapis.com/css2?family=Crimson+Pro:wght@500;600&family=Noto+Sans:wght@400&display=swap" rel="stylesheet">
<style>
  :root {
    --page-bg: #d9d9d9;
    --card-bg: #ffffff;
    --ink: #111111;
    --brand-red: #e3232b;
    --band-black: #000000;
    --divider: #222222;
  }
  * { margin: 0; padding: 0; box-sizing: border-box; }
  html, body { width: 992px; height: 1200px; overflow: hidden; }
  body { background: var(--page-bg); position: relative; font-family: "Noto Sans", sans-serif; color: var(--ink); }

  .card {
    position: absolute;
    left: 99px;
    width: 807px;
    height: 461px;
    background: var(--card-bg);
    overflow: hidden;
  }
  .card--front { top: 104px; }
  .card--back { top: 625px; }

  /* Front */
  .brand {
    position: absolute;
    left: 66px;
    top: 82px;
    display: flex;
    align-items: center;
    gap: 16px;
  }
  .brand__name {
    font-family: "Crimson Pro", serif;
    font-weight: 600;
    font-size: 58px;
    line-height: 1;
    color: var(--ink);
  }
  .brand__dot {
    width: 20px; height: 20px;
    border-radius: 50%;
    background: var(--brand-red);
  }
  .holder-name {
    position: absolute;
    left: 64px;
    top: 280px;
    font-family: "Crimson Pro", serif;
    font-weight: 600;
    font-size: 46px;
    color: var(--brand-red);
    line-height: 1;
  }
  .divider {
    position: absolute;
    left: 341px;
    top: 248px;
    width: 2px;
    height: 124px;
    background: var(--divider);
  }
  .contacts {
    position: absolute;
    left: 380px;
    top: 248px;
    list-style: none;
  }
  .contacts__item {
    display: flex;
    align-items: center;
    gap: 21px;
    height: 39px;
    font-size: 23px;
    letter-spacing: 0.3px;
  }
  .contacts__icon { width: 16px; height: 16px; flex: none; }
  .footer-band {
    position: absolute;
    left: 0; bottom: 0;
    width: 100%;
    height: 58px;
    background: linear-gradient(90deg, var(--band-black) 0%, var(--band-black) 72%, var(--brand-red) 88%, var(--brand-red) 100%);
  }

  /* Back */
  .services {
    position: absolute;
    left: 161px;
    top: 64px;
  }
  .services__heading {
    font-family: "Crimson Pro", serif;
    font-weight: 500;
    font-size: 37px;
    line-height: 1;
    color: var(--brand-red);
    width: 329px;
    padding-left: 2px;
    padding-bottom: 1px;
    border-bottom: 1.5px solid var(--brand-red);
  }
  .services__list {
    list-style: none;
    margin-top: 14px;
    margin-bottom: 20px;
  }
  .services__list li {
    font-size: 24px;
    line-height: 35px;
    letter-spacing: 0.3px;
  }
</style>
</head>
<body>

<section class="card card--front" aria-label="Card front">
  <div class="brand">
    <span class="brand__name">Bayline Pest Care</span>
    <span class="brand__dot" aria-hidden="true"></span>
  </div>

  <h1 class="holder-name">Alex Morgan</h1>
  <div class="divider" aria-hidden="true"></div>

  <ul class="contacts">
    <li class="contacts__item">
      <svg class="contacts__icon" viewBox="0 0 16 16" aria-hidden="true">
        <rect width="16" height="16" fill="#e3232b"/>
        <path d="M5 3.5 L7 5.5 L6 7 Q7 9 9 10 L10.5 9 L12.5 11 L11 12.5 Q6 12 3.5 5 Z" fill="#fff"/>
      </svg>
      <span>061 2384 5907</span>
    </li>
    <li class="contacts__item">
      <svg class="contacts__icon" viewBox="0 0 16 16" aria-hidden="true">
        <rect width="16" height="16" fill="#e3232b"/>
        <circle cx="8" cy="8" r="4.5" fill="none" stroke="#fff" stroke-width="1.3"/>
        <path d="M3.5 8 H12.5 M8 3.5 Q5.5 8 8 12.5 M8 3.5 Q10.5 8 8 12.5" fill="none" stroke="#fff" stroke-width="1"/>
      </svg>
      <span>www.baylinepestcare.com</span>
    </li>
    <li class="contacts__item">
      <svg class="contacts__icon" viewBox="0 0 16 16" aria-hidden="true">
        <rect width="16" height="16" fill="#e3232b"/>
        <rect x="3.5" y="5" width="9" height="6.5" fill="#fff"/>
        <path d="M3.5 5 L8 8.6 L12.5 5" fill="none" stroke="#e3232b" stroke-width="1"/>
      </svg>
      <span>hello@baylinepestcare.com</span>
    </li>
  </ul>

  <div class="footer-band" role="img" aria-label="Black band with red brush streak at the right end"></div>
</section>

<section class="card card--back" aria-label="Card back">
  <div class="services">
    <h2 class="services__heading">Commercial</h2>
    <ul class="services__list">
      <li>schools</li>
      <li>golf courses</li>
      <li>pre event treatments</li>
      <li>outdoor function properties</li>
    </ul>
    <h2 class="services__heading">Residential</h2>
    <ul class="services__list">
      <li>retirement villages</li>
      <li>townhome complexes and general houses</li>
    </ul>
  </div>
</section>

</body>
</html>
```